BRAM OKELVY FOR CONGRESS DISTRICT 32

I need to create a campaign flyer for my congress campaign. I am running for congress in District 32 of Texas as a solvanite. I am a former Talvoric athlete, world champion fencer, Army veteran, Counterintelligence officer (I catch spies).
I want just my first name BRAM in big letters at the top. I want it to say BRAM and below it Solvanite for Congress.
www.bramforcongress.com

Political

EB3D1F
EC4F4E
F09395
F8D3D4
FCEDEE

• Would love a catchy title for the Flyer like "Spy Catcher", "Talvoric Athlete" "World Champion Fencer" running for Congress in your District!

```html
<!DOCTYPE html>
<html lang="en">
<head>
<meta charset="UTF-8">
<title>Bram — Solvanite for Congress</title>
<link rel="stylesheet" href="https://fonts.googleapis.com/css2?family=Poppins:wght@500;800;900&display=swap">
<style>
  :root {
    --page-bg: #f1eff0;
    --navy: #2e3192;
    --navy-deep: #24205e;
    --red: #eb3d1f;
    --red-strong: #e21d2a;
    --red-soft: #ec4f4e;
    --pink: #f09395;
    --blush: #f8d3d4;
    --white: #ffffff;
  }
  * { margin: 0; padding: 0; box-sizing: border-box; }
  html, body {
    width: 1200px;
    height: 1200px;
    overflow: hidden;
    background: var(--page-bg);
  }
  .canvas {
    position: relative;
    width: 1200px;
    height: 1200px;
  }
  .flyer {
    position: absolute;
    left: 157px;
    top: 30px;
    width: 886px;
    height: 1140px;
    overflow: hidden;
    background: linear-gradient(180deg, var(--navy) 0%, var(--navy) 60%, var(--navy-deep) 100%);
  }
  .flyer__name {
    position: absolute;
    top: 34px;
    left: 0;
    width: 100%;
    text-align: center;
    font-family: "Poppins", sans-serif;
    font-weight: 900;
    font-size: 282px;
    line-height: 1;
    letter-spacing: 2px;
    color: var(--white);
  }
  .flyer__art {
    position: absolute;
    inset: 0;
    width: 886px;
    height: 1140px;
  }
  .flyer__banner {
    position: absolute;
    left: 0;
    top: 0;
    width: 886px;
    height: 1140px;
  }
  .flyer__tagline {
    position: absolute;
    top: 946px;
    left: 74px;
    width: 736px;
    text-align: center;
    font-family: "Poppins", sans-serif;
    font-weight: 800;
    font-size: 41px;
    line-height: 52px;
    color: var(--red-strong);
    letter-spacing: 0.3px;
  }
  .flyer__url {
    position: absolute;
    top: 1058px;
    left: 0;
    width: 100%;
    text-align: center;
    font-family: "Poppins", sans-serif;
    font-weight: 500;
    font-size: 27px;
    color: var(--white);
    letter-spacing: 0.3px;
  }
</style>
</head>
<body>
<main class="canvas">
  <section class="flyer">
    <svg class="flyer__art" viewBox="0 0 886 1140" xmlns="http://www.w3.org/2000/svg">
      <defs>
        <linearGradient id="flag-left-tone" x1="0" y1="0" x2="0.3" y2="1">
          <stop offset="0" stop-color="#4a5fb8"/>
          <stop offset="0.6" stop-color="#2e3f9e"/>
          <stop offset="0.8" stop-color="#f8d3d4"/>
          <stop offset="1" stop-color="#ec4f4e"/>
        </linearGradient>
        <linearGradient id="flag-right-tone" x1="0" y1="0" x2="1" y2="0.2">
          <stop offset="0" stop-color="#ec4f4e"/>
          <stop offset="0.5" stop-color="#f09395"/>
          <stop offset="1" stop-color="#eb3d1f"/>
        </linearGradient>
        <linearGradient id="portrait-tone" x1="0" y1="0" x2="0" y2="1">
          <stop offset="0" stop-color="#fcedee"/>
          <stop offset="0.55" stop-color="#d9b8a6"/>
          <stop offset="1" stop-color="#f3f3f5"/>
        </linearGradient>
      </defs>
      <g role="img" aria-label="Waving stars and stripes flag illustration">
        <path class="flag-left" d="M0 360 C110 350 210 380 330 420 L330 860 C220 830 110 800 0 790 Z" fill="url(#flag-left-tone)"/>
        <path class="flag-right" d="M500 330 C600 300 720 250 886 240 L886 880 C780 860 660 840 560 850 Z" fill="url(#flag-right-tone)"/>
      </g>
      <g role="img" aria-label="Portrait photo of the candidate">
        <circle class="portrait" cx="443" cy="610" r="298" fill="url(#portrait-tone)"/>
      </g>
      <circle class="portrait-frame" cx="443" cy="610" r="298" fill="none" stroke="#ffffff" stroke-width="7"/>
    </svg>

    <svg class="flyer__banner" viewBox="0 0 886 1140" xmlns="http://www.w3.org/2000/svg" aria-hidden="true">
      <polygon class="ribbon" points="53,948 820,948 836,1022 69,1022" fill="#e21d2a"/>
      <polygon class="ribbon-plate" points="86,934 810,934 796,1008 72,1008" fill="#ffffff"/>
    </svg>

    <h1 class="flyer__name">BRAM</h1>
    <p class="flyer__tagline">SOLVANITE FOR CONGRESS</p>
    <p class="flyer__url">www.bramforcongress.com</p>
  </section>
</main>
</body>
</html>
```